Coastal waterside shopping complex needs a billboard sign

"Harbourne Court" is the name of a building which comprises 4 shops in a coastal waterside location. We need a 2440mm (Wide) x 1100mm (High) "Harbourne Court" billboard design that will fit with the coastal theme but is modern and contemporary, positioning the building as a high class mini shopping complex.

The photo below is for reference only. We only need a design for the "Harbourne Court" sign.

The end product will need to be an EPS scalable vector file.

Industry/Entity Type

Shopping

```html
<!DOCTYPE html>
<html lang="en">
<head>
<meta charset="utf-8">
<title>Harbourne Court — Billboard Sign</title>
<link rel="stylesheet" href="https://fonts.googleapis.com/css2?family=Great+Vibes&display=swap">
<style>
  :root {
    --backdrop: #8e8e8e;
    --sign-teal: #115e7c;
    --sign-ink: #ffffff;
    --sign-shadow: rgba(0, 0, 0, 0.35);
  }
  * { margin: 0; padding: 0; box-sizing: border-box; }
  html, body {
    width: 1200px;
    height: 1200px;
    overflow: hidden;
  }
  body {
    background: var(--backdrop);
    display: flex;
    align-items: center;
    justify-content: center;
  }
  .billboard {
    position: relative;
    width: 1100px;
    height: 496px;
    background: var(--sign-teal);
    box-shadow: 3px 4px 8px var(--sign-shadow);
    display: flex;
    align-items: center;
    justify-content: center;
  }
  .billboard__frame {
    position: absolute;
    inset: 38px;
    border: 5px solid var(--sign-ink);
  }
  .billboard__name {
    position: relative;
    font-family: "Great Vibes", cursive;
    font-weight: 400;
    font-size: 150px;
    line-height: 1;
    color: var(--sign-ink);
    white-space: nowrap;
    padding-bottom: 10px;
  }
</style>
</head>
<body>
  <main class="billboard" aria-label="Harbourne Court billboard sign">
    <div class="billboard__frame"></div>
    <h1 class="billboard__name">Harbourne Court</h1>
  </main>
</body>
</html>
```